An insurance broker wants to represent the company's vision visually and textually.

My company, with a total of 10 employees, developed a vision this year. Now, we want to display this vision in the form of a two-meter-high visual that will be mounted on the wall. This ensures that the vision is always visible to our employees, as well as to our clients and partners when they visit our office.

Here's my idea: the vision will be accompanied by a fitting image, with the text of the vision itself elegantly written in a beautiful font. Our vision reads: "Every company always has a perfectly tailored future solution for greater financial security, freedom, and joy."

A bit about my company: we are an insurance broker, and our services are primarily designed for corporate clients.

```html
<!DOCTYPE html>
<html lang="en">
<head>
<meta charset="utf-8">
<title>Our Vision</title>
<link href="https://fonts.googleapis.com/css2?family=Saira+Semi+Condensed:wght@700&display=swap" rel="stylesheet">
<style>
  :root {
    --vision-yellow: #ffff00;
    --night-deep: #050505;
    --night-mid: #1c1c1c;
    --glow: #8a8a8a;
    --ground: #5a5a5a;
  }
  html, body {
    margin: 0;
    padding: 0;
    width: 685px;
    height: 1200px;
    overflow: hidden;
    background: var(--night-deep);
  }
  .poster {
    position: relative;
    width: 685px;
    height: 1200px;
    overflow: hidden;
  }
  .poster__photo {
    position: absolute;
    inset: 0;
    background:
      radial-gradient(ellipse 170px 260px at 330px 330px, var(--glow) 0%, rgba(80,80,80,0.45) 45%, rgba(0,0,0,0) 100%),
      radial-gradient(ellipse 420px 160px at 342px 1200px, var(--ground) 0%, rgba(40,40,40,0.6) 55%, rgba(0,0,0,0) 100%),
      linear-gradient(180deg, #3a3a3a 0%, var(--night-deep) 10%, var(--night-deep) 60%, var(--night-mid) 100%);
  }
  .poster__frame {
    position: absolute;
    left: 85px;
    top: 85px;
    width: 515px;
    height: 1030px;
    box-sizing: border-box;
    border: 21px solid var(--vision-yellow);
  }
  .vision {
    position: absolute;
    left: 0;
    top: 0;
    width: 685px;
    height: 1200px;
  }
  .vision__line {
    font-family: "Saira Semi Condensed", "Arial Narrow", sans-serif;
    font-weight: 700;
    font-size: 48px;
    fill: var(--vision-yellow);
  }
</style>
</head>
<body>
  <main class="poster">
    <div class="poster__photo" role="img" aria-label="Black and white night photograph of a person seen from behind holding up a glowing umbrella, with sparkling streams of rain swirling around them"></div>
    <div class="poster__frame"></div>
    <svg class="vision" viewBox="0 0 685 1200" aria-label="Every company always has a perfectly tailored future solution for greater financial security, freedom, and joy.">
      <text class="vision__line" x="138" y="562" textLength="115" lengthAdjust="spacingAndGlyphs">EVERY</text>
      <text class="vision__line" x="138" y="614" textLength="187" lengthAdjust="spacingAndGlyphs">COMPANY</text>
      <text class="vision__line" x="138" y="666" textLength="149" lengthAdjust="spacingAndGlyphs">ALWAYS</text>
      <text class="vision__line" x="138" y="717" textLength="321" lengthAdjust="spacingAndGlyphs">HAS A PERFECTLY</text>
      <text class="vision__line" x="138" y="769" textLength="175" lengthAdjust="spacingAndGlyphs">TAILORED</text>
      <text class="vision__line" x="138" y="821" textLength="144" lengthAdjust="spacingAndGlyphs">FUTURE</text>
      <text class="vision__line" x="138" y="873" textLength="185" lengthAdjust="spacingAndGlyphs">SOLUTION</text>
      <text class="vision__line" x="138" y="925" textLength="252" lengthAdjust="spacingAndGlyphs">FOR GREATER</text>
      <text class="vision__line" x="138" y="976" textLength="404" lengthAdjust="spacingAndGlyphs">FINANCIAL SECURITY,</text>
      <text class="vision__line" x="138" y="1028" textLength="380" lengthAdjust="spacingAndGlyphs">FREEDOM, AND JOY.</text>
    </svg>
  </main>
</body>
</html>
```